Brochure required

Looking at getting business brochure designed for my solar sales company. i will require a range of products to be listed on the brochure I require a simple/ elegent / professional looking brochure.

I am happy to provide designer with all the required information that must go into the brochure. otherwise please visit www.quillebartow.com.au and view the products which i would like to allocate into the brochure aswell as our company logo and a little about me section

```html
<!DOCTYPE html>
<html lang="en">
<head>
<meta charset="utf-8">
<title>Quillebartow – Energy Solutions Brochure</title>
<link rel="stylesheet" href="https://fonts.googleapis.com/css2?family=Poppins:wght@400;600;800&family=Roboto:wght@400;700&display=swap">
<style>
  :root{
    --backdrop:#ececec;
    --paper:#e9e9e9;
    --navy:#090e16;
    --yellow:#c4a91a;
    --yellow-light:#d8c22c;
    --ink:#0c0f14;
    --white:#ffffff;
    --sky:#8fb9d6;
    --panel:#1e2b42;
    --panel-deep:#0d1422;
  }
  *{box-sizing:border-box;margin:0;padding:0}
  html,body{width:1200px;height:840px;overflow:hidden;background:var(--backdrop)}
  .spread{position:absolute;left:50px;top:31px;width:1100px;height:778px;display:flex;box-shadow:0 12px 30px rgba(0,0,0,.18)}
  .page{position:relative;width:550px;height:778px;background:var(--paper);overflow:hidden}
  .page svg.shapes{position:absolute;inset:0;width:100%;height:100%}
  .brand{position:absolute;display:flex;flex-direction:column;font-family:"Poppins",sans-serif;color:var(--ink)}
  .brand-line{display:flex;align-items:center;gap:8px}
  .brand-dot{width:18px;height:18px;background:var(--yellow-light)}
  .brand-name{font-weight:800;font-size:30px;letter-spacing:.5px;line-height:1}
  .brand-tagline{font-weight:400;font-size:12.5px;letter-spacing:2px;margin-top:4px}
  .back .brand{left:36px;top:30px}
  .front .brand{left:36px;top:36px}
  .contact{position:absolute;left:60px;top:560px;font-family:"Roboto",sans-serif;color:var(--ink)}
  .contact h2{font-family:"Poppins",sans-serif;font-weight:600;font-size:20px;letter-spacing:.5px;margin-bottom:14px}
  .contact li{list-style:none;display:flex;align-items:center;gap:10px;font-size:12.5px;margin-bottom:9px}
  .contact svg{width:13px;height:13px;fill:var(--ink)}
  .cover-title{position:absolute;right:34px;top:560px;text-align:right;color:var(--white);font-family:"Poppins",sans-serif;line-height:1}
  .cover-title .t1{font-weight:800;font-size:66px;letter-spacing:1px}
  .cover-title .t2{font-weight:400;font-size:50px;letter-spacing:2px;margin-top:-2px}
  .cover-title .t3{font-weight:400;font-size:21px;letter-spacing:2px;margin-top:4px}
  .footer-url{position:absolute;left:36px;bottom:40px;font-family:"Roboto",sans-serif;font-size:12px;color:var(--ink);letter-spacing:.3px}
</style>
</head>
<body>
<main class="spread">
  <section class="page back">
    <svg class="shapes" viewBox="0 0 550 778" preserveAspectRatio="none" aria-hidden="true">
      <polygon fill="var(--paper)" points="0,0 550,0 550,778 0,778"/>
      <polygon fill="var(--navy)" points="380,0 550,0 550,560 0,370 0,300"/>
      <polygon fill="var(--yellow)" points="0,370 550,560 550,778 0,778"/>
    </svg>
    <div class="brand">
      <div class="brand-line"><span class="brand-dot"></span><span class="brand-name">Quillebartow</span></div>
      <span class="brand-tagline">Solutions for a changing world</span>
    </div>
    <div class="contact">
      <h2>CONTACT</h2>
      <ul>
        <li><svg viewBox="0 0 24 24"><path d="M6.6 10.8a15 15 0 0 0 6.6 6.6l2.2-2.2a1 1 0 0 1 1-.25 11.4 11.4 0 0 0 3.6.57 1 1 0 0 1 1 1V20a1 1 0 0 1-1 1A17 17 0 0 1 3 4a1 1 0 0 1 1-1h3.5a1 1 0 0 1 1 1c0 1.25.2 2.45.57 3.57a1 1 0 0 1-.25 1z"/></svg>0400 555 123</li>
        <li><svg viewBox="0 0 24 24"><path d="M2 5h20v14H2z M2 5l10 8 10-8" fill="none" stroke="#0c0f14" stroke-width="2"/></svg>info@quillebartow.com</li>
        <li><svg viewBox="0 0 24 24"><circle cx="12" cy="12" r="10" fill="none" stroke="#0c0f14" stroke-width="2"/><path d="M2 12h20M12 2c3 3 3 17 0 20M12 2c-3 3-3 17 0 20" fill="none" stroke="#0c0f14" stroke-width="1.6"/></svg>www.quillebartow.com.au</li>
      </ul>
    </div>
  </section>

  <section class="page front">
    <svg class="shapes" viewBox="0 0 550 778" preserveAspectRatio="none">
      <defs>
        <linearGradient id="solarPhoto" x1="0" y1="0" x2="0" y2="1">
          <stop offset="0" stop-color="var(--sky)"/>
          <stop offset=".28" stop-color="#c9d6de"/>
          <stop offset=".36" stop-color="#3d4c5e"/>
          <stop offset=".6" stop-color="var(--panel)"/>
          <stop offset="1" stop-color="var(--panel-deep)"/>
        </linearGradient>
      </defs>
      <polygon fill="var(--paper)" points="0,0 550,0 550,778 0,778"/>
      <polygon role="img" aria-label="Photo of a technician in a hard hat and safety vest cleaning rooftop solar panels under a cloudy sky" fill="url(#solarPhoto)" points="320,0 550,0 550,778 275,778 40,528"/>
      <polygon fill="var(--yellow-light)" points="0,498 40,528 275,778 0,778"/>
    </svg>
    <div class="brand">
      <div class="brand-line"><span class="brand-dot"></span><span class="brand-name">Quillebartow</span></div>
      <span class="brand-tagline">Solutions for a changing world</span>
    </div>
    <div class="cover-title">
      <div class="t1">ENERGY</div>
      <div class="t2">SOLUTIONS</div>
      <div class="t3">For A CHANGING WORLD</div>
    </div>
    <div class="footer-url">www.quillebartow.com.au</div>
  </section>
</main>
</body>
</html>
```